Financial Broker firm looking for Brochure design/Pdf-document

Job Type
Brochure Design/PDF-Document
Task Outline
Create a Brochure Design that also works for sending as pdf-document.
Task Description
We need a combined corporate brochure (Booklet style) to give out to potential clients as well as sending it to potential clients through Internet as pdf-document.
We need a background template with pictures and colors that gives the impression of professionalism, trustworthiness and seriousness. Attached text in English but the text will be translated into different languages to fit different markets. Therefore we would like to receive one template including the text and one without any text (but with the logo). Please inform us where (any) pictures and/or photos on the template have been taken from in order for us to buy and use them legally.
About Us
Our company Quelvo Brokerage AB is a financial brokerage company who provides a diversity of services for different selected partners (www.quelvobrokerage.example).
Target Market
Companies on all levels, domestic or international
Requirements
Must Have:
-The text and logo attached below
Industry/Entity Type
Financial
Look and feel
Each slider illustrates characteristics of the customer's brand and the style your logo design should communicate.

```html
<!DOCTYPE html>
<html lang="en">
<head>
<meta charset="utf-8">
<title>Quelvo Brokerage AB — Brochure Cover</title>
<link rel="stylesheet" href="https://fonts.googleapis.com/css2?family=Exo+2:wght@300;700&display=swap">
<style>
  :root {
    --paper: #ffffff;
    --brand-blue: #1a4f9c;
    --band-blue: #1467c8;
    --band-blue-light: #2f8ae0;
    --accent-orange: #f7a600;
    --accent-orange-light: #ffc23a;
    --sky-top: #5f9fdc;
    --sky-bottom: #cfe4f5;
    --grass: #6fae35;
    --faint-wash: #e9eef4;
    --logo-ink: #1c2330;
  }
  * { margin: 0; padding: 0; box-sizing: border-box; }
  html, body {
    width: 809px;
    height: 1200px;
    overflow: hidden;
    background: var(--paper);
  }
  .cover {
    position: relative;
    width: 809px;
    height: 1200px;
    background: var(--paper);
    font-family: "Exo 2", "Trebuchet MS", sans-serif;
    overflow: hidden;
  }
  .cover-art {
    position: absolute;
    inset: 0;
    width: 809px;
    height: 1200px;
  }
  .background-scene {
    position: absolute;
    left: 0;
    top: 690px;
    width: 809px;
    height: 440px;
    background: linear-gradient(160deg, rgba(233,238,244,0) 0%, var(--faint-wash) 45%, rgba(220,230,240,0.6) 75%, rgba(255,255,255,0) 100%);
  }
  .tagline {
    position: absolute;
    left: 478px;
    top: 470px;
    color: var(--brand-blue);
    font-weight: 300;
    line-height: 1;
  }
  .tagline-lead {
    display: block;
    font-size: 40px;
    letter-spacing: 0.5px;
  }
  .tagline-mid {
    display: block;
    font-size: 34px;
    margin-top: 10px;
  }
  .tagline-key {
    display: block;
    font-size: 76px;
    margin-top: 4px;
    letter-spacing: 1px;
  }
  .brand {
    position: absolute;
    left: 440px;
    top: 818px;
    display: flex;
    align-items: center;
    gap: 12px;
  }
  .brand-name {
    font-weight: 700;
    font-size: 34px;
    color: var(--logo-ink);
    letter-spacing: 0.5px;
    white-space: nowrap;
  }
  .brand-dot {
    width: 26px;
    height: 26px;
    border-radius: 50%;
    background: var(--band-blue);
  }
  .footer-band {
    position: absolute;
    left: 0;
    bottom: 0;
    width: 809px;
    height: 58px;
    background: var(--accent-orange);
  }
</style>
</head>
<body>
  <main class="cover">
    <div class="background-scene" role="img" aria-label="Faint business photo of hands reviewing financial charts"></div>

    <svg class="cover-art" viewBox="0 0 809 1200" xmlns="http://www.w3.org/2000/svg">
      <defs>
        <linearGradient id="blue-band" x1="0" y1="1" x2="1" y2="0">
          <stop offset="0" stop-color="var(--band-blue-light)"/>
          <stop offset="1" stop-color="var(--band-blue)"/>
        </linearGradient>
        <linearGradient id="photo-tones" x1="0" y1="0" x2="0" y2="1">
          <stop offset="0" stop-color="var(--sky-top)"/>
          <stop offset="0.55" stop-color="var(--sky-bottom)"/>
          <stop offset="0.75" stop-color="var(--grass)"/>
          <stop offset="1" stop-color="#4f8f25"/>
        </linearGradient>
      </defs>
      <g class="arc-accents">
        <circle class="arc-orange" cx="-40" cy="-130" r="690" fill="var(--accent-orange)"/>
        <circle class="arc-orange-inner" cx="-40" cy="-130" r="672" fill="var(--paper)"/>
        <circle class="arc-blue" cx="-20" cy="-150" r="660" fill="url(#blue-band)"/>
      </g>
      <g class="hero-photo" role="img" aria-label="Photo of cupped hands holding coins with a young green sprout, blue sky and meadow behind">
        <circle cx="-80" cy="-150" r="620" fill="url(#photo-tones)"/>
      </g>
    </svg>

    <h1 class="tagline">
      <span class="tagline-lead">A Partner</span>
      <span class="tagline-mid">in need as in</span>
      <span class="tagline-key">success</span>
    </h1>

    <div class="brand">
      <span class="brand-name">QUELVO BROKERAGE</span>
      <span class="brand-dot"></span>
    </div>

    <div class="footer-band"></div>
  </main>
</body>
</html>
```